Business Card Design - ChoiceCraft

Looking for creative, modern design, two sided for ChoiceCraft that is consistent with color and feel of website www.choicecraftpro.net.
Updates

Back of card will be used to promote products or have a quote revolving around decisions, change, leadership, innovation, creativity. Back should also have space to promote website, but optional to use the icon. Front of the card will need to use the icon and have standard place for name, job title, phone and email. We are not looking to put a mailing address or fax. Also want space to place a few words/phrase explaining what we do...such as individual growth and organizational development or tools, training, information...in addition, want the facebook icon small on the front somewhere as we are also on facebook.

Vector file uploaded of icon.

Target Market(s)

Professional coaching for individual growth and organizational development

Industry/Entity Type

Business

Requirements
Must have
• Icon...see attached.

```html
<!DOCTYPE html>
<html lang="en">
<head>
<meta charset="utf-8">
<title>ChoiceCraft Business Card</title>
<link rel="stylesheet" href="https://fonts.googleapis.com/css2?family=Tinos:wght@400;700&family=Arimo:wght@400;700&display=swap">
<style>
  :root {
    --bg: #d9dadc;
    --card: #ffffff;
    --brand-blue: #1d7fc4;
    --deep-blue: #0d5fa8;
    --light-blue: #3fb6ea;
    --accent-blue: #2a9fd8;
    --ink: #2a2a2a;
    --ink-soft: #333333;
    --mark: #bcd6ec;
    --mark-edge: #5aa6dc;
  }
  * { margin: 0; padding: 0; box-sizing: border-box; }
  html, body { width: 1200px; height: 1096px; overflow: hidden; }
  body { background: var(--bg); position: relative; font-family: "Tinos", "Times New Roman", serif; }

  .card {
    position: absolute;
    height: 460px;
    background: var(--card);
    overflow: hidden;
    box-shadow: 0 2px 6px rgba(0,0,0,.18);
  }
  .card--front { left: 64px; top: 64px; width: 806px; }
  .card--back  { left: 322px; top: 564px; width: 854px; }

  /* Front */
  .brand { position: absolute; left: 178px; top: 39px; display: flex; align-items: center; gap: 18px; }
  .brand__dot { width: 160px; height: 160px; border-radius: 50%; background: var(--mark); border: 5px solid var(--mark-edge); flex: none; }
  .brand__name { font-weight: 700; font-size: 40px; color: var(--brand-blue); letter-spacing: .5px; }

  .tagline {
    position: absolute; right: 400px; top: 250px;
    text-align: right; font-size: 20px; line-height: 23px; color: var(--ink);
  }
  .divider { position: absolute; left: 426px; top: 236px; width: 1.5px; height: 102px; background: var(--ink); }

  .contacts { position: absolute; left: 443px; top: 238px; list-style: none; font-size: 19.5px; line-height: 24.5px; color: var(--ink); }
  .contacts li { display: flex; align-items: center; gap: 9px; }
  .contacts svg { width: 14px; height: 14px; flex: none; }
  .social-square { width: 13px; height: 13px; background: var(--deep-blue); flex: none; }

  .band { position: absolute; left: 0; top: 0; width: 806px; height: 460px; }
  .person { position: absolute; left: 101px; top: 396px; color: #fff; font-size: 30px; font-weight: 700; }
  .person__title { font-size: 22px; font-weight: 400; }

  /* Back */
  .quotes { position: absolute; left: 44px; top: 38px; list-style: none; font-family: "Arimo", Arial, sans-serif; }
  .quote { position: relative; padding-left: 46px; height: 81px; }
  .quote__dot { position: absolute; left: 0; top: 4px; width: 30px; height: 30px; border-radius: 50%; background: var(--mark); border: 2px solid var(--mark-edge); }
  .quote__text { font-size: 20.5px; color: var(--ink-soft); position: relative; padding-left: 18px; }
  .quote__text::before { content: "\201C"; position: absolute; left: 0; top: -10px; font-family: "Tinos", serif; font-weight: 700; font-size: 32px; }
  .quote__text::after { content: "\201D"; font-family: "Tinos", serif; font-weight: 700; font-size: 32px; line-height: 0; position: relative; top: 14px; margin-left: 2px; }
  .quote__author { font-size: 20px; color: var(--ink-soft); padding-left: 18px; margin-top: 5px; }
  .quote__author b { color: var(--accent-blue); }

  .back-mark { position: absolute; left: 588px; top: 262px; width: 150px; height: 150px; border-radius: 50%; background: var(--mark); border: 6px solid var(--mark-edge); }
</style>
</head>
<body>

<section class="card card--front" aria-label="Card front">
  <svg class="band" viewBox="0 0 806 460" aria-hidden="true">
    <defs>
      <linearGradient id="band-fill" x1="0" y1="0" x2="1" y2="0">
        <stop offset="0" stop-color="#0d5fa8"/>
        <stop offset="1" stop-color="#1b86cc"/>
      </linearGradient>
    </defs>
    <path d="M0 368 Q403 340 806 368" fill="none" stroke="var(--light-blue)" stroke-width="4"/>
    <path d="M0 380 Q403 352 806 380 L806 460 L0 460 Z" fill="url(#band-fill)"/>
  </svg>

  <div class="brand">
    <span class="brand__dot"></span>
    <span class="brand__name">ChoiceCraft</span>
  </div>

  <p class="tagline">Supporting individual growth<br>and organizational development<br>or tools, training, information</p>
  <span class="divider"></span>

  <ul class="contacts">
    <li><svg viewBox="0 0 14 14"><path d="M3 1 L5.5 4 L4 5.5 C5 7.8 6.5 9.3 8.5 10 L10 8.5 L13 11 L11 13 C6 12.5 1.5 8 1 3 Z" fill="none" stroke="#2a2a2a" stroke-width="1.3"/></svg>555-318-042</li>
    <li><svg viewBox="0 0 14 14"><rect x="1" y="3" width="12" height="9" fill="none" stroke="#2a2a2a" stroke-width="1.3"/><path d="M1 3 L7 8 L13 3" fill="none" stroke="#2a2a2a" stroke-width="1.3"/></svg>hello@choicecraftpro.net</li>
    <li><svg viewBox="0 0 14 14"><circle cx="7" cy="7" r="6" fill="none" stroke="#2a2a2a" stroke-width="1.3"/><ellipse cx="7" cy="7" rx="2.6" ry="6" fill="none" stroke="#2a2a2a" stroke-width="1"/><path d="M1 7 H13" stroke="#2a2a2a" stroke-width="1"/></svg>www.choicecraftpro.net</li>
    <li><span class="social-square"></span>/choicecraftpro</li>
  </ul>

  <p class="person">Your Name, <span class="person__title">Title</span></p>
</section>

<section class="card card--back" aria-label="Card back">
  <ul class="quotes">
    <li class="quote"><span class="quote__dot"></span>
      <p class="quote__text">Try not to become a man of success, but rather a man of value.</p>
      <p class="quote__author">- <b>Martin Ellory</b></p></li>
    <li class="quote"><span class="quote__dot"></span>
      <p class="quote__text">The only constant is change.</p>
      <p class="quote__author">- <b>Theron Vale</b></p></li>
    <li class="quote"><span class="quote__dot"></span>
      <p class="quote__text">We are what we repeatedly do. Excellence is not an act, it is a habit.</p>
      <p class="quote__author">- <b>Corin Apsley</b></p></li>
    <li class="quote"><span class="quote__dot"></span>
      <p class="quote__text">Simplicity is the ultimate sophistication.</p>
      <p class="quote__author">- <b>Lucian Marvello</b></p></li>
    <li class="quote"><span class="quote__dot"></span>
      <p class="quote__text">Life is not fair - get used to it.</p>
      <p class="quote__author">- <b>Walt Henning</b></p></li>
  </ul>
  <span class="back-mark"></span>
</section>

</body>
</html>
```